Business Card Design for BrightvaleMedia.com

--I need a business card design for my company BrightvaleMedia.com

I have attached my logo...I want the brightvale media logo on the front of the business card, and then I want The Quillstone Chief on the back of it with my information.

I would like to see a light colored background as well as a dark colored background

FRONT:
BRIGHTVALE MEDIA LOGO
248 N. Larkmoor
3rd Floor
San Diego CA 92173
www.BrightvaleMedia.com

Advanced Website & App Development
Websites, Apps, Online Voucher Systems

Leading Edge Marketing Services
SMS, VB, SMM, SEM,

BACK:
QUILLSTONE CHIEF LOGO
Dorian Pelletta
The Quillstone Chief
Call Or Text: 619-555-0148
Dorian@QuillstoneChief.example
www.QuillstoneChief.example

Target Market(s)

small business owners

Industry/Entity Type

Business Consultant

Contact Information for Business Card

FRONT:
BRIGHTVALE MEDIA LOGO
248 N. Larkmoor
3rd Floor
San Diego CA 92173
www.BrightvaleMedia.com

SMS, VB, SMM, SEM,

BACK:
QUILLSTONE CHIEF LOGO
Dorian Pelletta
The Quillstone Chief
Dorian@QuillstoneChief.example
www.QuillstoneChief.example

Requirements
Must have
• add this quote on it somewhere, anywhere,preferrably on back
• "The Fastest Way To Success Is To Take Action”
• — Dorian Pelletta, Quillstone Chief
Nice to have
• open
Should not have
• red

```html
<!DOCTYPE html>
<html lang="en">
<head>
<meta charset="utf-8">
<title>Brightvale Media Business Card</title>
<link rel="stylesheet" href="https://fonts.googleapis.com/css2?family=Source+Sans+3:ital,wght@0,400;0,600;1,400&display=swap">
<style>
  :root {
    --stage: #000000;
    --card-light: #f3f3f3;
    --card-dark: #0a6fa6;
    --brand-blue: #1a6ea5;
    --ink: #3d3d3d;
    --white: #ffffff;
  }
  html, body {
    margin: 0;
    padding: 0;
    width: 1200px;
    height: 900px;
    overflow: hidden;
    background: var(--stage);
    font-family: "Source Sans 3", Arial, sans-serif;
  }
  .stage {
    position: relative;
    width: 1200px;
    height: 900px;
  }
  .card {
    position: absolute;
    top: 200px;
    width: 310px;
    height: 502px;
    box-sizing: border-box;
  }
  .card--personal {
    left: 265px;
    background: var(--card-light);
    border-radius: 62px 0 62px 0;
  }
  .card--company {
    left: 641px;
    width: 309px;
    background: var(--card-dark);
    border-radius: 0 62px 0 62px;
    color: var(--white);
  }
  .wordmark {
    position: absolute;
    left: 0;
    right: 0;
    text-align: center;
    font-weight: 600;
    font-size: 28px;
    letter-spacing: 2px;
    margin: 0;
  }
  .card--personal .wordmark {
    top: 76px;
    color: var(--brand-blue);
  }
  .card--company .wordmark {
    top: 82px;
    color: var(--white);
  }
  .quote {
    position: absolute;
    left: 37px;
    right: 37px;
    top: 172px;
    margin: 0;
    font-size: 14px;
    line-height: 19px;
    color: var(--ink);
  }
  .quote__text {
    margin: 0 0 6px;
    font-style: italic;
  }
  .quote__author {
    margin: 0;
    color: var(--brand-blue);
  }
  .person {
    position: absolute;
    left: 37px;
    top: 338px;
  }
  .person__name {
    margin: 0;
    font-size: 18px;
    font-weight: 600;
    color: var(--brand-blue);
    line-height: 22px;
  }
  .person__title {
    margin: 0;
    font-size: 14px;
    color: var(--ink);
    line-height: 18px;
  }
  .contact-list {
    position: absolute;
    left: 37px;
    top: 411px;
    margin: 0;
    padding: 0;
    list-style: none;
    font-size: 14px;
    color: var(--ink);
  }
  .contact-list li {
    display: flex;
    align-items: center;
    height: 18px;
  }
  .contact-list svg {
    width: 10px;
    height: 10px;
    margin-right: 8px;
    margin-left: 0;
    fill: var(--brand-blue);
  }
  .company-info {
    position: absolute;
    left: 29px;
    top: 278px;
    font-size: 15px;
    font-weight: 600;
    line-height: 18px;
  }
  .company-info p {
    margin: 0 0 11px;
  }
</style>
</head>
<body>
<main class="stage">
  <section class="card card--personal" aria-label="Personal side">
    <p class="wordmark">QUILLSTONE CHIEF</p>
    <blockquote class="quote">
      <p class="quote__text">“The Fastest Way To Success Is To Take Action”</p>
      <p class="quote__author">— Dorian Pelletta, Quillstone Chief</p>
    </blockquote>
    <div class="person">
      <p class="person__name">Dorian Pelletta</p>
      <p class="person__title">The Quillstone Chief</p>
    </div>
    <ul class="contact-list">
      <li>
        <svg viewBox="0 0 10 10" aria-hidden="true"><path d="M2 0.5 L3.6 2.6 L2.7 3.6 Q3.6 5.6 6.2 7.2 L7.2 6.3 L9.5 7.8 L8.6 9.5 Q4.5 9.6 1.5 5.8 Q0 3.5 0.5 1.5 Z"/></svg>
        619-555-0148
      </li>
      <li>
        <svg viewBox="0 0 10 10" aria-hidden="true"><path d="M0.5 2 H9.5 V8.5 H0.5 Z M1 2.6 L5 5.6 L9 2.6 V3.4 L5 6.4 L1 3.4 Z" fill-rule="evenodd"/></svg>
        Dorian@QuillstoneChief.example
      </li>
      <li>
        <svg viewBox="0 0 10 10" aria-hidden="true"><circle cx="5" cy="5" r="4.6"/></svg>
        www.QuillstoneChief.example
      </li>
    </ul>
  </section>

  <section class="card card--company" aria-label="Company side">
    <p class="wordmark">BRIGHTVALE MEDIA</p>
    <div class="company-info">
      <p>248 N. Larkmoor<br>3rd Floor, San Diego CA 92173</p>
      <p>www.BrightvaleMedia.com</p>
      <p>Advanced Website &amp; App Development<br>Websites, Apps, Online Voucher Systems</p>
      <p>Leading Edge Marketing Services<br>SMS | VB | SMM | SEM,</p>
    </div>
  </section>
</main>
</body>
</html>
```